Australian Trucking Company Requires Professional Looking Stationary

We require a professional looking stationary design that incorporates our newly designed logo.

Our business, called "Brell Haulage Contracting", provides contracting work, transport and logistics to business in Western Australia particularly with links to the mining sector.

We are a small business looking to expand and our new logo and our new stationary will help develop our brand image in our market place.

Target Market(s)

Businesses and Corporation with links to the Mining Sector

Industry/Entity Type

Small Business

Requirements
Must have
• The letterhead must have the following details:
The new logo

Text saying: "Brell Holdings Pty Ltd (ACN 582 316 907) ATF The Brell Discretionary Trust T/AS"
"ABN 71 834 209 553"
Address "P.O Box 817 Wattlegrove WA, 6958"
Phone: 08 9352 7140
Email: brellhaul@mailbox-example.com.au

The text on the letterhead should be editable as the details are likely to change in the near future. Provision should be made for a website address all though one isn't available at the moment.

The styling, layout and font text is entirely up to the designer.

```html
<!DOCTYPE html>
<html lang="en">
<head>
<meta charset="utf-8">
<title>Brell Haulage Contracting – Business Card</title>
<link href="https://fonts.googleapis.com/css2?family=Open+Sans:wght@400;600;700&display=swap" rel="stylesheet">
<style>
  :root {
    --backdrop: #e7e3de;
    --card-white: #ffffff;
    --brand-red: #c4161c;
    --red-deep: #7d0a0e;
    --red-bright: #d8262b;
    --ink: #333333;
    --ink-soft: #555555;
    --rule: #d4d4d4;
    --on-red: #ffffff;
  }
  * { box-sizing: border-box; margin: 0; padding: 0; }
  html, body { width: 1200px; height: 426px; overflow: hidden; }
  body {
    background: var(--backdrop);
    font-family: "Open Sans", Arial, sans-serif;
    color: var(--ink);
    position: relative;
  }
  .card {
    position: absolute;
    width: 545px;
    height: 297px;
    border-radius: 22px;
    box-shadow: 0 4px 10px rgba(0,0,0,0.25);
    overflow: hidden;
  }
  .card--front { left: 52px; top: 55px; background: var(--card-white); }
  .card--back {
    left: 604px; top: 48px;
    background: radial-gradient(ellipse at 40% 50%, var(--red-bright) 0%, #a9141a 55%, var(--red-deep) 100%);
    display: flex; align-items: center; justify-content: center;
  }
  .brand {
    position: absolute;
    left: 0; right: 0; top: 62px;
    display: flex; align-items: center; justify-content: center; gap: 12px;
  }
  .brand__mark { width: 22px; height: 22px; background: var(--brand-red); }
  .brand__name {
    font-weight: 700;
    font-size: 30px;
    color: var(--brand-red);
    letter-spacing: 0.5px;
  }
  .person {
    position: absolute; left: 0; right: 0; top: 150px;
    text-align: center; font-size: 17px; font-weight: 600; color: var(--ink-soft);
  }
  .person__role { font-size: 13px; font-weight: 400; }
  .contact {
    position: absolute; left: 0; right: 0; top: 200px;
    text-align: center; font-size: 13px; color: var(--ink); line-height: 20px;
  }
  .contact__row { display: flex; justify-content: center; align-items: center; gap: 6px; }
  .contact__item { display: inline-flex; align-items: center; gap: 4px; }
  .contact__item + .contact__item { margin-left: 8px; }
  .icon { width: 11px; height: 11px; fill: var(--ink); }
  .divider {
    position: absolute; left: 54px; right: 54px; top: 245px;
    border-top: 1px solid var(--rule);
  }
  .legal {
    position: absolute; left: 0; right: 0; top: 251px;
    text-align: center; font-size: 11.5px; line-height: 19px; color: var(--ink);
  }
  .back-brand {
    color: var(--on-red);
    font-weight: 700;
    font-size: 34px;
    text-align: center;
    line-height: 1.2;
    letter-spacing: 0.5px;
  }
</style>
</head>
<body>
  <section class="card card--front">
    <div class="brand">
      <span class="brand__mark"></span>
      <span class="brand__name">Brell Haulage Contracting</span>
    </div>

    <p class="person">Persons name, <span class="person__role">Manager</span></p>

    <div class="contact">
      <div class="contact__row">
        <span class="contact__item">
          <svg class="icon" viewBox="0 0 12 12" aria-hidden="true"><path d="M2.5 0.5 L4.5 0.5 L5 3 L3.6 4 Q4.6 6.6 7.5 8 L8.5 6.7 L11 7.2 L11 9.5 Q10.5 11.5 8.5 11 Q1.5 9 0.8 2.5 Q0.8 0.5 2.5 0.5 Z"/></svg>
          08 9352 7140
        </span>
        <span class="contact__item">
          <svg class="icon" viewBox="0 0 12 12" aria-hidden="true"><path d="M0.5 2.5 H11.5 V9.5 H0.5 Z M1.5 3.5 V8.5 H10.5 V3.5 L6 6.6 Z M2 3.5 L6 5.8 L10 3.5 Z" fill-rule="evenodd"/></svg>
          brellhaul@mailbox-example.com.au
        </span>
      </div>
      <div class="contact__row">
        <span class="contact__item">
          <svg class="icon" viewBox="0 0 12 12" aria-hidden="true"><path d="M6 0.8 L11.5 6 H9.8 V11 H7.2 V7.8 H4.8 V11 H2.2 V6 H0.5 Z"/></svg>
          P.O Box 817 Wattlegrove WA, 6958
        </span>
      </div>
    </div>

    <div class="divider"></div>

    <p class="legal">
      Brell Holdings Pty Ltd (ACN 582 316 907) ATF The Brell Discretionary Trust T/AS<br>
      ABN 71 834 209 553
    </p>
  </section>

  <section class="card card--back">
    <p class="back-brand">Brell Haulage<br>Contracting</p>
  </section>
</body>
</html>
```